Tampa Bay fishing guide needs stunning website.

I currently have a site - www.reelcoveguide.net which I personally put together using the Pagely platform and I am looking for a redesign on a different platform (Sitecraft?) that will allow me to easily create landing pages in the future. Would like to have a block for visitors to opt in to newsletter. Need social media links on all pages.

I would like to let my visitors know that I am able to handle their fishing charter needs here in the Tampa Bay area, if I'm not available for the dates they are looking to go I can refer them to a reputable captain in the area.

Target Market(s)

United States

Industry/Entity Type

Tourism

Coding

Coded - Design and coding required

Number of Pages Required

5+ page

Font styles to use
Sans Serif

Colors
0355a3
3176b5
85abd2
fbf289

Requirements
Must have
• Mobile Responsive, Ability to insert Vantor Metrics, Chatterbox pixels, ability to add custom landing pages in future
Nice to have
• Clean, easy navigation

```html
<!DOCTYPE html>
<html lang="en">
<head>
<meta charset="utf-8">
<title>Capt. Wade Harlan – Tampa Bay Fishing Charters</title>
<link rel="stylesheet" href="https://fonts.googleapis.com/css2?family=Open+Sans:wght@400;600&family=Roboto+Condensed:wght@400;700&display=swap">
<style>
:root{
  --blue:#0355a3;
  --blue-mid:#3176b5;
  --blue-soft:#85abd2;
  --yellow:#fbf289;
  --yellow-band:#fbf5a6;
  --yellow-panel:#f9ef8f;
  --grey:#ebebeb;
  --ink:#111;
  --text:#555;
  --white:#fff;
}
*{box-sizing:border-box;margin:0;padding:0}
html,body{width:1200px;height:2990px;overflow:hidden}
body{font-family:"Open Sans",Arial,sans-serif;color:var(--ink);background:var(--white);position:relative}
.cond{font-family:"Roboto Condensed","Arial Narrow",sans-serif}
.btn{display:inline-flex;align-items:center;justify-content:center;gap:10px;background:var(--blue);color:var(--white);font-family:"Roboto Condensed","Arial Narrow",sans-serif;font-weight:700;font-size:19px;text-decoration:none;border-radius:3px}
.section-title{font-family:"Roboto Condensed","Arial Narrow",sans-serif;font-weight:400;font-size:46px;text-align:center;letter-spacing:.5px}
.section-title span{color:var(--blue)}

/* header */
.site-header{height:126px;display:flex;align-items:center;justify-content:space-between;padding:0 72px 0 78px}
.brand{display:flex;align-items:center;gap:12px;font-family:"Roboto Condensed","Arial Narrow",sans-serif;font-weight:700;font-size:40px;color:var(--blue)}
.brand-dot{width:26px;height:26px;border-radius:50%;background:var(--blue-soft)}
.main-nav{display:flex;gap:34px;font-family:"Roboto Condensed","Arial Narrow",sans-serif;font-size:18px;color:#444}
.main-nav a{color:inherit;text-decoration:none}
.main-nav a.active{color:var(--blue)}

/* hero */
.hero{height:574px;position:relative;background:linear-gradient(120deg,#0b2a4a 0%,#14477a 40%,#1d5a8e 60%,#3a4e5f 80%,#6b5a48 100%)}
.hero-title{position:absolute;left:78px;top:230px;background:rgba(10,25,45,.55);padding:14px 14px 14px 12px}
.hero-title h1{font-family:"Roboto Condensed","Arial Narrow",sans-serif;font-weight:400;font-size:56px;color:var(--white);line-height:1.1}
.hero-title p{font-size:22px;color:var(--white);margin-top:8px}
.hero-cta{position:absolute;left:78px;top:413px;width:198px;height:52px;background:var(--yellow);color:var(--blue);font-family:"Roboto Condensed","Arial Narrow",sans-serif;font-weight:700;font-size:20px;display:flex;align-items:center;justify-content:center;border-radius:3px}

/* welcome */
.welcome{height:330px;text-align:center;padding-top:46px}
.welcome p{width:720px;margin:22px auto 0;font-size:15.5px;line-height:28px;color:var(--text)}
.welcome .btn{width:168px;height:52px;margin-top:26px;font-family:"Open Sans",Arial,sans-serif;font-weight:400;font-size:18px}

/* rates */
.rates{height:400px;background:var(--grey);padding-top:44px}
.rates .section-title{color:var(--blue)}
.rate-list{display:flex;margin:30px 0 0 80px;gap:0}
.rate{display:flex;width:542px}
.rate-photo{width:210px;height:138px;background:linear-gradient(135deg,#5d7a8f,#c9d3cf 60%,#8aa2b2)}
.rate-info{margin-left:40px;font-size:15.5px;line-height:28px}
.rate-info .name,.rate-info .price{color:var(--blue)}
.rate-info .desc{color:var(--text);width:260px;margin-top:4px}
.rate-info a{color:var(--blue);text-decoration:underline}
.rates .center{text-align:center;margin-top:28px}
.rates .btn{width:156px;height:52px}

/* locations */
.locations{height:580px;text-align:center;padding-top:58px}
.locations .lead{font-size:19px;margin-top:14px}
.locations .sub{font-size:16.5px;margin-top:4px}
.location-list{display:flex;gap:40px;margin:36px 0 0 78px}
.location{width:322px}
.location-map{height:195px;background:linear-gradient(160deg,#a7c6ee,#d9e3ef 55%,#eef0ec)}
.location-name{height:55px;background:var(--blue);color:var(--white);font-family:"Roboto Condensed","Arial Narrow",sans-serif;font-weight:700;font-size:23px;display:flex;align-items:center;justify-content:center}
.locations .btn{width:154px;height:56px;margin-top:46px}

/* gift card */
.gift{height:452px;background:var(--grey);position:relative;padding-top:64px}
.gift .sub{text-align:center;font-size:15.5px;color:var(--text);margin-top:4px}
.field{position:absolute;background:var(--white);font-size:14.5px;color:#999;padding:10px 22px}
.gift-note{position:absolute;left:812px;top:178px;font-size:15px;color:var(--text);font-family:"Roboto Condensed","Arial Narrow",sans-serif}
.submit{position:absolute;left:462px;top:342px;width:624px;height:40px;background:var(--blue);color:var(--white);font-family:"Roboto Condensed","Arial Narrow",sans-serif;font-size:24px;display:flex;align-items:center;justify-content:center;border-radius:3px}
.gift-accent{position:absolute;left:528px;top:382px;width:148px;height:60px;background:linear-gradient(90deg,var(--blue-mid),var(--yellow) 60%,var(--blue))}

/* contact */
.contact{height:473px;background:var(--yellow-band);padding-top:78px}
.contact-panel{width:558px;height:326px;margin-left:322px;background:var(--yellow-panel);padding-top:40px}
.contact-panel h2{font-family:"Roboto Condensed","Arial Narrow",sans-serif;font-weight:400;font-size:40px;text-align:center}
.contact-row{display:flex;align-items:center;gap:12px;font-size:15.5px;position:absolute}
.icon{width:46px;height:46px;border-radius:50%;background:var(--white);display:flex;align-items:center;justify-content:center}
.social{position:absolute;display:flex;gap:26px;left:508px;top:2773px}
.social span{width:44px;height:44px;border-radius:50%;display:block}

/* footer */
.site-footer{height:55px;background:var(--blue);color:var(--white);font-size:14px;display:flex;align-items:center;justify-content:center}
.site-footer b{color:var(--yellow);font-weight:600}
</style>
</head>
<body>

<header class="site-header">
  <div class="brand"><span class="brand-dot"></span>Wade Harlan</div>
  <nav class="main-nav">
    <a class="active" href="#">HOME</a>
    <a href="#">ABOUT US</a>
    <a href="#">PICK UP LOCATIONS</a>
    <a href="#">RATES</a>
    <a href="#">CONTACT US</a>
    <a href="#">GIFT CARD</a>
  </nav>
</header>

<section class="hero" role="img" aria-label="Angler on a boat deck fighting a large fish in deep blue water">
  <div class="hero-title">
    <h1>CAPT. WADE HARLAN</h1>
    <p>Come fish with Tampa Bay, FL fishing guide, Tampa Bay fishing charter</p>
  </div>
  <div class="hero-cta">CONTACT US NOW</div>
</section>

<section class="welcome">
  <h2 class="section-title">WELCOME TO <span>CAPT. WADE HARLAN</span></h2>
  <p>Capt. Wade was born and raised in the Tampa Bay area and fell in love with fishing as a very young boy. He has guided some of the world's top name celebrities and politicians. Through his passion and hard work he has earned a living as a full time guide.</p>
  <a class="btn" href="#">READ MORE</a>
</section>

<section class="rates">
  <h2 class="section-title">RATES</h2>
  <div class="rate-list">
    <div class="rate">
      <div class="rate-photo" role="img" aria-label="Anglers holding a large catch on a boat"></div>
      <div class="rate-info">
        <div class="name">Half Day : 1-2 People</div>
        <div class="price">4 hr &nbsp;| &nbsp;$399.00</div>
        <div class="desc">Enjoy a half day charter on Tampa Bay with Capt. Wade.</div>
        <a href="#">BOOK NOW</a>
      </div>
    </div>
    <div class="rate">
      <div class="rate-photo" role="img" aria-label="Two anglers showing a big fish on deck"></div>
      <div class="rate-info">
        <div class="name">Half Day : 4 People</div>
        <div class="price">4 hr &nbsp;| &nbsp;$499.00</div>
        <div class="desc">Enjoy a half day charter on Tampa Bay with Capt. Wade.</div>
        <a href="#">BOOK NOW</a>
      </div>
    </div>
  </div>
  <div class="center"><a class="btn" href="#">VIEW ALL
    <svg width="20" height="18" viewBox="0 0 20 18"><path d="M2 2l7 7-7 7M10 2l7 7-7 7" fill="none" stroke="#fff" stroke-width="3"/></svg></a></div>
</section>

<section class="locations">
  <h2 class="section-title">PICK UP <span>LOCATIONS</span></h2>
  <p class="lead">Four Convenient Locations on Every Corner of Tampa Bay</p>
  <p class="sub">No matter where you might be staying in the Tampa Bay area, Capt. Wade can pick you up nearby.</p>
  <div class="location-list">
    <div class="location">
      <div class="location-map" role="img" aria-label="Map of the Bayline Marina pick up point"></div>
      <div class="location-name">BAYLINE MARINA</div>
    </div>
    <div class="location">
      <div class="location-map" role="img" aria-label="Map of the Heron Cove pick up point in Ruskin"></div>
      <div class="location-name">HERON COVE - RUSKIN</div>
    </div>
    <div class="location">
      <div class="location-map" role="img" aria-label="Map of the Causeway Boat Ramp pick up point"></div>
      <div class="location-name">CAUSEWAY BOAT RAMP</div>
    </div>
  </div>
  <a class="btn" href="#">VIEW ALL
    <svg width="20" height="18" viewBox="0 0 20 18"><path d="M2 2l7 7-7 7M10 2l7 7-7 7" fill="none" stroke="#fff" stroke-width="3"/></svg></a>
</section>

<section class="gift">
  <h2 class="section-title">GIFT <span>CARD</span></h2>
  <p class="sub">Give the Perfect Gift - The Gift of Memories!</p>
  <div class="field" style="left:118px;top:168px;width:332px;height:40px">E - Mail</div>
  <div class="field" style="left:118px;top:222px;width:332px;height:40px">From</div>
  <div class="field" style="left:118px;top:274px;width:332px;height:40px">To</div>
  <div class="field" style="left:118px;top:328px;width:332px;height:40px">Contact No.</div>
  <div class="field" style="left:462px;top:168px;width:330px;height:40px">Gift Amount</div>
  <div class="field" style="left:462px;top:222px;width:624px;height:94px">Message</div>
  <div class="gift-note">GIFT BETWEEN 100 USD &amp; 700 USD</div>
  <div class="gift-accent" role="img" aria-label="Decorative block pattern in blue and yellow"></div>
  <div class="submit">SUBMIT</div>
</section>

<section class="contact">
  <div class="contact-panel">
    <h2>KEEP IN TOUCH</h2>
  </div>
</section>

<div class="contact-row" style="left:366px;top:2650px">
  <span class="icon"><svg width="20" height="20" viewBox="0 0 24 24"><path d="M6.6 10.8a15 15 0 006.6 6.6l2.2-2.2a1 1 0 011-.25 11 11 0 003.6.6 1 1 0 011 1V20a1 1 0 01-1 1A17 17 0 013 4a1 1 0 011-1h3.5a1 1 0 011 1 11 11 0 00.6 3.6 1 1 0 01-.25 1z" fill="#0355a3"/></svg></span>
  <b style="font-weight:600">813-555-0142</b>
</div>
<div class="contact-row" style="left:556px;top:2650px">
  <span class="icon"><svg width="22" height="18" viewBox="0 0 22 18"><rect x="1.5" y="2" width="19" height="14" rx="2" fill="none" stroke="#0355a3" stroke-width="2"/><path d="M2 3l9 7 9-7" fill="none" stroke="#0355a3" stroke-width="2"/></svg></span>
  captwade@harlanmail.net
</div>
<div class="contact-row" style="left:366px;top:2720px">
  <span class="icon"><svg width="20" height="20" viewBox="0 0 24 24"><path d="M3 5l6-2 6 2 6-2v16l-6 2-6-2-6 2z M9 3v16 M15 5v16" fill="none" stroke="#0355a3" stroke-width="2" stroke-linejoin="round"/></svg></span>
  Lorem Ipsum is dummy text of the printing.
</div>
<div class="social" aria-label="Social media links">
  <span style="background:#1d4a8c" aria-label="Social link one"></span>
  <span style="background:#1da1e0" aria-label="Social link two"></span>
  <span style="background:#e0412f" aria-label="Social link three"></span>
</div>

<footer class="site-footer">
  <p>© <b>Capt. Wade Harlan</b> &nbsp;- 2016 &nbsp;All rights reserved.</p>
</footer>

</body>
</html>
```